Northfield Builders Guild Business card

We are looking for a new business card design with photo included.
Our business is a nonprofit construction contractor membership organization. We offer business education, assist with business setup and licensing, provide safety training, and provide a member directory.
URL: www.builderslinkguild.org
Color code:
CMYK: 0 cyan, 42 magenta, 100 yellow, 0 black for Print.
Hexidecimal: #FF9900
RGB: R 255; G 153; B 0

```html
<!DOCTYPE html>
<html lang="en">
<head>
<meta charset="utf-8">
<title>Northfield Builders Guild – Business Card</title>
<link href="https://fonts.googleapis.com/css2?family=Open+Sans:wght@400;800&family=Michroma&display=swap" rel="stylesheet">
<style>
  :root {
    --brand-orange: #F99A1C;
    --ink-dark: #333233;
    --ink-text: #2b2b2b;
    --card-white: #ffffff;
    --backdrop: #e9e7e4;
    --square-line: #8a8a8a;
  }
  html, body {
    margin: 0;
    padding: 0;
    overflow: hidden;
  }
  body {
    width: 1200px;
    height: 649px;
    background: var(--backdrop);
    position: relative;
    font-family: "Open Sans", sans-serif;
  }
  .card {
    position: absolute;
    background: var(--card-white);
    box-shadow: 0 3px 10px rgba(0,0,0,0.22);
    overflow: hidden;
  }
  /* Front face */
  .card-front {
    left: 142px;
    top: 116px;
    width: 560px;
    height: 319px;
  }
  .wordmark {
    position: absolute;
    font-family: "Open Sans", sans-serif;
    font-weight: 800;
    color: var(--ink-dark);
    text-transform: uppercase;
    line-height: 1;
    text-align: center;
    letter-spacing: -1px;
  }
  .card-front .wordmark {
    left: 74px;
    top: 112px;
    width: 296px;
  }
  .wordmark .line-top { display: block; font-size: 42px; }
  .wordmark .line-bottom { display: block; font-size: 29px; margin-top: 6px; }
  .front-address {
    position: absolute;
    left: 21px;
    top: 292px;
    font-size: 11px;
    color: var(--ink-text);
    white-space: nowrap;
  }
  .social-squares {
    position: absolute;
    left: 324px;
    top: 286px;
    display: flex;
    gap: 3px;
  }
  .social-squares span {
    width: 18px;
    height: 18px;
    border: 1.5px solid var(--square-line);
    border-radius: 2px;
    box-sizing: border-box;
  }
  /* Back face */
  .card-back {
    left: 557px;
    top: 234px;
    width: 564px;
    height: 322px;
  }
  .card-back .corner-swoosh {
    position: absolute;
    left: 0;
    top: 0;
  }
  .card-back .wordmark {
    left: 64px;
    top: 140px;
    width: 232px;
  }
  .card-back .wordmark .line-top { font-size: 33px; }
  .card-back .wordmark .line-bottom { font-size: 23px; margin-top: 5px; }
  .person {
    position: absolute;
    right: 32px;
    top: 120px;
    text-align: right;
  }
  .person-name {
    font-family: "Michroma", sans-serif;
    color: var(--brand-orange);
    font-size: 12px;
    letter-spacing: 2.5px;
    line-height: 1;
  }
  .person-title {
    font-size: 8.5px;
    color: var(--ink-text);
    margin-top: 2px;
  }
  .contact-list {
    position: absolute;
    right: 26px;
    top: 174px;
    margin: 0;
    padding: 0;
    list-style: none;
  }
  .contact-list li {
    display: flex;
    justify-content: flex-end;
    align-items: center;
    gap: 5px;
    font-size: 11px;
    color: var(--ink-text);
    height: 24.5px;
  }
  .contact-list svg {
    width: 18px;
    height: 18px;
    flex: none;
  }
</style>
</head>
<body>

  <section class="card card-front" aria-label="Card front">
    <div class="wordmark">
      <span class="line-top">Northfield</span>
      <span class="line-bottom">Builders Guild</span>
    </div>
    <p class="front-address">418 Alder Street NW Suite 210 Fairhaven MI 49612</p>
    <div class="social-squares" aria-hidden="true">
      <span></span><span></span><span></span>
    </div>
  </section>

  <section class="card card-back" aria-label="Card back">
    <svg class="corner-swoosh" width="564" height="322" viewBox="0 0 564 322" aria-hidden="true">
      <path d="M421 0 C490 2 545 50 564 123 V0 Z" fill="var(--brand-orange)"/>
      <path d="M0 203 C20 270 60 315 109 322 H0 Z" fill="var(--brand-orange)"/>
    </svg>

    <div class="wordmark">
      <span class="line-top">Northfield</span>
      <span class="line-bottom">Builders Guild</span>
    </div>

    <div class="person">
      <div class="person-name">DANA WHITFIELD</div>
      <div class="person-title">CEO/Managing Director</div>
    </div>

    <ul class="contact-list">
      <li>555-014-2288
        <svg viewBox="0 0 24 24" aria-hidden="true"><path d="M5 3 L9 3 L10.5 8 L8 10 C9.5 13 11 14.5 14 16 L16 13.5 L21 15 L21 19 C21 20 20 21 19 21 C11 21 3 13 3 5 C3 4 4 3 5 3 Z" fill="none" stroke="var(--brand-orange)" stroke-width="2" stroke-linejoin="round"/><path d="M14 3 A7 7 0 0 1 21 10 M14 7 A3 3 0 0 1 17 10" fill="none" stroke="var(--brand-orange)" stroke-width="1.8"/></svg>
      </li>
      <li>555-014-2288
        <svg viewBox="0 0 24 24" aria-hidden="true"><rect x="6" y="3" width="12" height="5" fill="var(--brand-orange)"/><rect x="2" y="8" width="20" height="9" rx="2" fill="var(--brand-orange)"/><rect x="6" y="13" width="12" height="9" fill="#fff" stroke="var(--brand-orange)" stroke-width="1.8"/><path d="M8.5 16.5 H15.5 M8.5 19 H15.5" stroke="var(--brand-orange)" stroke-width="1.4"/></svg>
      </li>
      <li>dana@builderslinkguild.org
        <svg viewBox="0 0 24 24" aria-hidden="true"><rect x="2" y="5" width="20" height="14" fill="var(--brand-orange)"/><path d="M2 5 L12 13 L22 5 M2 19 L9 11 M22 19 L15 11" fill="none" stroke="#fff" stroke-width="1.4"/></svg>
      </li>
      <li>www.builderslinkguild.org
        <svg viewBox="0 0 24 24" aria-hidden="true"><g fill="none" stroke="var(--brand-orange)" stroke-width="1.5"><circle cx="12" cy="12" r="9.5"/><ellipse cx="12" cy="12" rx="4.5" ry="9.5"/><path d="M2.5 12 H21.5 M4 7 H20 M4 17 H20 M12 2.5 V21.5"/></g></svg>
      </li>
    </ul>
  </section>

</body>
</html>
```